Business cards and stationary design

We just completed the design of our new logo and we need to print new business cards and letterhead for our nonprofit. We are looking for a fresh new design that shows off our new logo. On letterhead, we must have a column on the right or left to include our Board of Directors (up to 45 names) (see attachment)

Industry/Entity Type

Non-Profit

Contact Information for Business Card

Standard business card with name, title, Company name, mailing address phone numbers, email address and website. Tagline on back "Bringing the homeless home"

Font styles to use
Sans Serif

Requirements
Must have
• include pertinent information above
• new logo
• fonts compatible with logo
• should use logo colors only
Nice to have
• tag lines

```html
<!DOCTYPE html>
<html lang="en">
<head>
<meta charset="utf-8">
<title>Shelter Bridge Center – Business Card</title>
<link href="https://fonts.googleapis.com/css2?family=Courier+Prime:wght@400;700&family=Lato:wght@400&display=swap" rel="stylesheet">
<style>
  :root {
    --backdrop: #8c8c8c;
    --card-light: #ffffff;
    --card-dark: #333333;
    --teal: #1b7f9b;
    --red: #e8141c;
    --ink: #222222;
  }
  html, body {
    margin: 0;
    padding: 0;
    width: 1200px;
    height: 900px;
    overflow: hidden;
    background: var(--backdrop);
  }
  .card {
    position: absolute;
    top: 306px;
    width: 438px;
    height: 271px;
    border-radius: 12px;
    box-sizing: border-box;
  }
  .card--front { left: 150px; background: var(--card-light); }
  .card--back  { left: 609px; background: var(--card-dark); }

  .brand {
    position: absolute;
    display: flex;
    align-items: center;
    gap: 10px;
    font-family: "Courier Prime", monospace;
    font-weight: 400;
    color: var(--teal);
    white-space: nowrap;
  }
  .brand__mark {
    background: var(--teal);
    flex: none;
  }
  .card--front .brand { right: 24px; top: 68px; font-size: 22px; }
  .card--front .brand__mark { width: 28px; height: 28px; }
  .card--back .brand {
    left: 60px;
    right: 60px;
    justify-content: center;
    top: 163px;
    font-size: 22px;
  }
  .card--back .brand__mark { width: 28px; height: 28px; }

  .person {
    position: absolute;
    left: 22px;
    top: 156px;
    right: 22px;
  }
  .person__name {
    margin: 0;
    font-family: "Courier Prime", monospace;
    font-weight: 700;
    font-size: 15px;
    letter-spacing: 0.5px;
    color: var(--teal);
  }
  .person__name .surname { color: var(--red); }
  .person__role {
    display: flex;
    align-items: center;
    margin-top: 1px;
    font-family: "Lato", sans-serif;
    font-size: 12.5px;
    color: var(--ink);
  }
  .person__role::after {
    content: "";
    flex: 1;
    height: 1px;
    background: var(--red);
    margin-left: 2px;
    margin-top: 4px;
  }

  .contact {
    position: absolute;
    left: 24px;
    top: 197px;
    margin: 0;
    padding: 0;
    list-style: none;
    font-family: "Lato", sans-serif;
    font-size: 12.5px;
    line-height: 16.5px;
    color: var(--ink);
  }
  .contact li { display: flex; align-items: center; gap: 4px; }
  .contact svg { width: 10px; height: 10px; fill: var(--teal); }

  .address {
    position: absolute;
    right: 28px;
    top: 213px;
    margin: 0;
    font-style: normal;
    text-align: right;
    font-family: "Lato", sans-serif;
    font-size: 12.5px;
    line-height: 16.5px;
    color: var(--ink);
  }
</style>
</head>
<body>
  <section class="card card--front">
    <div class="brand"><span class="brand__mark"></span>shelter bridge center</div>

    <div class="person">
      <h1 class="person__name">MARCUS <span class="surname">REED</span></h1>
      <div class="person__role">Managing Director</div>
    </div>

    <ul class="contact">
      <li>
        <svg viewBox="0 0 10 10" aria-hidden="true"><path d="M1 2.5C1 1.5 2 1 5 1s4 .5 4 1.5V4H7V3H3v1H1zM2 5h6l1 4H1z"/></svg>
        444 555 6688
      </li>
      <li>
        <svg viewBox="0 0 10 10" aria-hidden="true"><path d="M1 2h8v6H1z"/><path d="M1 2l4 3.2L9 2" fill="none" stroke="#fff" stroke-width="1"/></svg>
        info@youremail.com
      </li>
      <li>
        <svg viewBox="0 0 10 10" aria-hidden="true"><circle cx="5" cy="5" r="4.5"/></svg>
        www.websitename.com
      </li>
    </ul>

    <address class="address">421, Address line here<br>Country Name,45452</address>
  </section>

  <section class="card card--back">
    <div class="brand"><span class="brand__mark"></span>shelter bridge center</div>
  </section>
</body>
</html>
```